Design a New Business Card for Our Company

We are looking for fresh, unique, and a modern business card that reflects our roots as digital marketing agency focused on SEM.

Industry/Entity Type

Marketing

Contact Information for Business Card

looking for very unique out of the box designs. clean and modern that compliments our logo

Requirements
Must have
• colors should match our logo
• Front should have name, address, email, and phone/fax of the person, phone/fax are the same number
• back should have our url

```html
<!DOCTYPE html>
<html lang="en">
<head>
<meta charset="utf-8">
<title>Brightpath Media – Business Card</title>
<link rel="stylesheet" href="https://fonts.googleapis.com/css2?family=Source+Sans+3:wght@400;600;700&display=swap">
<style>
  :root {
    --brand-blue: #5596d0;
    --ink-blue: #3f80c4;
    --ink-grey: #8a8a8a;
    --logo-grey: #9b9b9b;
    --mark-faint: #e9ecf3;
    --card-white: #ffffff;
    --stage: #ecebe8;
  }
  * { box-sizing: border-box; margin: 0; padding: 0; }
  html, body { width: 1200px; height: 675px; overflow: hidden; }
  body {
    background: var(--stage);
    font-family: "Source Sans 3", "Helvetica Neue", Arial, sans-serif;
    position: relative;
  }
  .card {
    position: absolute;
    top: 190px;
    width: 510px;
    height: 292px;
    box-shadow: 0 6px 18px rgba(0,0,0,0.12);
    overflow: hidden;
  }
  .card--front { left: 70px; background: var(--card-white); }
  .card--back  { left: 620px; background: var(--brand-blue); }

  /* Front */
  .brand {
    position: absolute;
    display: flex;
    align-items: center;
    gap: 10px;
  }
  .brand__dot { border-radius: 50%; flex: none; }
  .brand__name { font-weight: 700; letter-spacing: -0.5px; white-space: nowrap; }
  .card--front .brand { left: 28px; top: 26px; }
  .card--front .brand__dot { width: 34px; height: 34px; background: var(--logo-grey); }
  .card--front .brand__name { font-size: 30px; color: var(--logo-grey); }

  .faint-mark {
    position: absolute;
    right: 36px;
    top: 112px;
    width: 210px;
    height: 210px;
    border-radius: 50%;
    background: var(--mark-faint);
  }

  .contact {
    position: absolute;
    left: 30px;
    top: 104px;
    font-size: 13px;
    line-height: 16px;
    color: var(--ink-grey);
  }
  .contact__company { color: var(--ink-blue); font-weight: 600; }
  .contact__lines { list-style: none; margin-top: 6px; }
  .contact__lines li { display: flex; align-items: center; gap: 7px; height: 17px; }
  .contact__icon { width: 12px; height: 12px; flex: none; }

  .person {
    position: absolute;
    right: 30px;
    top: 104px;
    text-align: right;
  }
  .person__name { font-size: 18px; font-weight: 700; color: var(--ink-blue); }
  .person__role { font-size: 14px; color: var(--ink-grey); }

  /* Back */
  .card--back .brand { left: 50%; top: 108px; transform: translateX(-50%); }
  .card--back .brand__dot { width: 44px; height: 44px; background: var(--card-white); }
  .card--back .brand__name { font-size: 44px; color: var(--card-white); }
  .back__url {
    position: absolute;
    bottom: 36px;
    width: 100%;
    text-align: center;
    font-size: 17px;
    letter-spacing: 0.3px;
    color: var(--card-white);
  }
</style>
</head>
<body>
  <section class="card card--front" aria-label="Card front">
    <div class="brand">
      <span class="brand__dot"></span>
      <span class="brand__name">Brightpath Media</span>
    </div>
    <div class="faint-mark" aria-hidden="true"></div>

    <div class="contact">
      <p class="contact__company">Brightpath Media</p>
      <p>N. 12 Cedar Avenue, Suite 200,</p>
      <p>Boise, ID 83702</p>
      <ul class="contact__lines">
        <li>
          <svg class="contact__icon" viewBox="0 0 12 12" aria-label="Phone"><circle cx="6" cy="6" r="6" fill="var(--brand-blue)"/><path d="M4 3.2c.4-.3.8-.2 1 .2l.4.8c.1.3 0 .6-.2.8l-.3.2c.3.8.9 1.4 1.7 1.7l.2-.3c.2-.2.5-.3.8-.2l.8.4c.4.2.5.6.2 1-.4.6-1 .8-1.6.6C5.5 7.9 4.1 6.5 3.6 5c-.2-.6 0-1.3.4-1.8z" fill="#fff"/></svg>
          <span>555.210.4477</span>
        </li>
        <li>
          <svg class="contact__icon" viewBox="0 0 12 12" aria-label="Fax"><circle cx="6" cy="6" r="6" fill="var(--brand-blue)"/><rect x="3" y="5" width="6" height="3.5" rx="0.6" fill="#fff"/><rect x="4.2" y="3" width="3.6" height="2" fill="#fff"/></svg>
          <span>555.210.4477</span>
        </li>
        <li>
          <svg class="contact__icon" viewBox="0 0 12 12" aria-label="Email"><circle cx="6" cy="6" r="6" fill="var(--brand-blue)"/><rect x="3" y="4" width="6" height="4" fill="#fff"/><path d="M3 4l3 2.2L9 4" stroke="var(--brand-blue)" stroke-width="0.7" fill="none"/></svg>
          <span>hello@brightpathmedia.com</span>
        </li>
        <li>
          <svg class="contact__icon" viewBox="0 0 12 12" aria-label="Website"><circle cx="6" cy="6" r="6" fill="var(--brand-blue)"/><circle cx="6" cy="6" r="3" fill="none" stroke="#fff" stroke-width="0.8"/><path d="M3 6h6M6 3v6" stroke="#fff" stroke-width="0.7"/></svg>
          <span>www.brightpathmedia.com</span>
        </li>
      </ul>
    </div>

    <div class="person">
      <p class="person__name">Dana Whitfield</p>
      <p class="person__role">Owner</p>
    </div>
  </section>

  <section class="card card--back" aria-label="Card back">
    <div class="brand">
      <span class="brand__dot"></span>
      <span class="brand__name">Brightpath Media</span>
    </div>
    <p class="back__url">www.brightpathmedia.com</p>
  </section>
</body>
</html>
```